Hair salon Business Card

Beauty Salon
I would like to see designs using sky blue and a soft orange. Mainly I would like my name ( Silkridge Hair Studio ) used as the design

Industry/Entity Type

Business

Contact Information for Business Card

Silkridge Hair Studio
318 E Maple Hyw #14
Linden Vale, Ca 90415
555 014-2716

```html
<!DOCTYPE html>
<html lang="en">
<head>
<meta charset="utf-8">
<title>Silkridge Hair Studio – Business Card</title>
<link rel="stylesheet" href="https://fonts.googleapis.com/css2?family=Questrial&family=Open+Sans:wght@400&display=swap">
<style>
  :root {
    --stage: #3a302b;
    --card-dark: #1c1c1e;
    --card-blue: #3f7fd0;
    --brand-sky: #5cb0ec;
    --brand-orange: #e39a4a;
    --text-light: #e6e6e6;
    --white: #ffffff;
  }
  * { margin: 0; padding: 0; box-sizing: border-box; }
  html, body {
    width: 1200px;
    height: 844px;
    overflow: hidden;
    background: var(--stage);
  }
  .canvas {
    position: relative;
    width: 1200px;
    height: 844px;
  }
  .card {
    position: absolute;
    width: 520px;
    height: 297px;
    border-radius: 3px;
    box-shadow: 0 14px 30px rgba(0, 0, 0, 0.45);
  }
  /* Contact side */
  .card--contact {
    left: 60px;
    top: 420px;
    background: var(--card-dark);
  }
  .brand-lockup {
    position: absolute;
    left: 40px;
    top: 118px;
    width: 250px;
    display: flex;
    align-items: center;
    gap: 12px;
  }
  .brand-lockup__text {
    display: flex;
    flex-direction: column;
    align-items: center;
  }
  .brand-lockup__name {
    font-family: "Questrial", sans-serif;
    font-size: 26px;
    line-height: 1.1;
    color: var(--brand-sky);
    white-space: nowrap;
  }
  .brand-lockup__sub {
    font-family: "Questrial", sans-serif;
    font-size: 12px;
    letter-spacing: 2px;
    color: var(--text-light);
    margin-top: 2px;
  }
  .brand-lockup__dot {
    flex: none;
    width: 14px;
    height: 14px;
    border-radius: 50%;
    background: var(--brand-orange);
  }
  .divider {
    position: absolute;
    left: 310px;
    top: 88px;
    width: 1px;
    height: 120px;
    background: linear-gradient(to bottom, transparent, var(--brand-orange) 25%, var(--brand-orange) 75%, transparent);
  }
  .contact {
    position: absolute;
    left: 332px;
    top: 108px;
    font-family: "Open Sans", sans-serif;
    font-style: normal;
    font-size: 14px;
    line-height: 1.55;
    color: var(--text-light);
  }
  .contact__phone {
    display: flex;
    align-items: center;
    gap: 8px;
    margin-bottom: 8px;
  }
  .contact__icon { width: 12px; height: 12px; }
  /* Name side */
  .card--name {
    left: 620px;
    top: 170px;
    background: var(--card-blue);
    display: flex;
    flex-direction: column;
    align-items: center;
    justify-content: center;
  }
  .card--name .brand-name {
    font-family: "Questrial", sans-serif;
    font-size: 46px;
    line-height: 1.1;
    color: var(--white);
  }
  .card--name .brand-sub {
    font-family: "Questrial", sans-serif;
    font-size: 18px;
    letter-spacing: 3px;
    color: var(--white);
    margin-top: 4px;
  }
</style>
</head>
<body>
<main class="canvas">
  <section class="card card--contact" aria-label="Business card, contact side">
    <div class="brand-lockup">
      <div class="brand-lockup__text">
        <span class="brand-lockup__name">Silkridge</span>
        <span class="brand-lockup__sub">HAIR STUDIO</span>
      </div>
      <span class="brand-lockup__dot" aria-hidden="true"></span>
    </div>
    <div class="divider" aria-hidden="true"></div>
    <address class="contact">
      <div class="contact__phone">
        <svg class="contact__icon" viewBox="0 0 24 24" aria-hidden="true">
          <path fill="#e39a4a" d="M6.6 10.8a15.1 15.1 0 0 0 6.6 6.6l2.2-2.2a1 1 0 0 1 1-.25 11.4 11.4 0 0 0 3.6.57 1 1 0 0 1 1 1V20a1 1 0 0 1-1 1A17 17 0 0 1 3 4a1 1 0 0 1 1-1h3.5a1 1 0 0 1 1 1c0 1.25.2 2.45.57 3.57a1 1 0 0 1-.25 1z"/>
        </svg>
        <span>555 014-2716</span>
      </div>
      <div>318 E Maple Hyw #14</div>
      <div>Linden Vale, Ca 90415</div>
    </address>
  </section>

  <section class="card card--name" aria-label="Business card, name side">
    <span class="brand-name">Silkridge</span>
    <span class="brand-sub">HAIR STUDIO</span>
  </section>
</main>
</body>
</html>
```